Small Business Broker Business Card Design

A business card design for a small business brokerage, which is a financial service, not unlike real estate brokerage, but for small businesses such as laundromats, pizza shops, restaurants, cleaners etc. The designs should all be simple, more conservative in nature, using the colors and font of the logo. Again, think real estate Brokerage as a business context
Contact Information for Business Card
Name: Glen R. Harlow. Title: Small Business Advisor. Email: g.harlow@bayfieldcapitalworks.example. Mobile: (555) 274-3918. Office: (555) 806-2147. www.bayfieldcapitalworks.example

```html
<!DOCTYPE html>
<html lang="en">
<head>
<meta charset="utf-8">
<title>Bayfield Capital Works – Business Card</title>
<link rel="stylesheet" href="https://fonts.googleapis.com/css2?family=Montserrat:wght@400;500;600;700&display=swap">
<style>
  :root {
    --navy: #1b3a6d;
    --navy-deep: #163260;
    --navy-pattern: #2c5a9a;
    --green: #8cc63f;
    --white: #ffffff;
    --stage: #b9b9b9;
  }
  * { box-sizing: border-box; margin: 0; padding: 0; }
  html, body { width: 1200px; height: 788px; overflow: hidden; }
  body {
    background: var(--stage);
    font-family: "Montserrat", sans-serif;
    position: relative;
  }
  .card {
    position: absolute;
    top: 239px;
    width: 540px;
    height: 310px;
    border-radius: 16px;
    overflow: hidden;
    background: var(--navy);
    box-shadow: 0 10px 24px rgba(0,0,0,0.25);
  }
  .card--front { left: 40px; }
  .card--back { left: 620px; }

  /* front */
  .edge-band { position: absolute; bottom: 0; height: 10px; }
  .edge-band--green { left: 0; width: 57%; background: var(--green); }
  .edge-band--white { right: 0; width: 43%; background: var(--white); }
  .corner-tab {
    position: absolute; top: 0; right: 52px; width: 28px; height: 12px;
    background: var(--green);
  }
  .person { position: absolute; top: 34px; right: 72px; text-align: right; }
  .person__name {
    color: var(--green); font-weight: 700; font-size: 25px;
    letter-spacing: 1px; text-transform: uppercase;
  }
  .person__title { color: var(--white); font-weight: 500; font-size: 13px; margin-top: 2px; }
  .brand {
    position: absolute; left: 36px; top: 92px;
    display: flex; align-items: center; gap: 10px;
  }
  .brand__square { width: 26px; height: 26px; background: var(--green); }
  .brand__name {
    color: var(--white); font-weight: 700; font-size: 15px;
    letter-spacing: 0.6px; text-transform: uppercase;
  }
  .brand__tagline {
    position: absolute; left: 36px; top: 124px;
    color: var(--green); font-weight: 600; font-size: 7.5px;
    letter-spacing: 0.8px; text-transform: uppercase;
  }
  .address {
    position: absolute; left: 36px; top: 158px;
    color: var(--white); font-size: 13px; line-height: 1.45;
  }
  .contacts { position: absolute; left: 36px; top: 206px; list-style: none; }
  .contacts li {
    display: flex; align-items: center; gap: 8px;
    color: var(--white); font-size: 12px; line-height: 19px;
  }
  .contacts svg { width: 11px; height: 11px; flex: none; }

  /* back */
  .back-pattern {
    position: absolute; inset: 0;
    background: linear-gradient(135deg, var(--navy-pattern) 0%, var(--navy) 45%, var(--navy-deep) 100%);
  }
  .back-brand {
    position: absolute; right: 28px; bottom: 58px;
    display: flex; align-items: center; gap: 8px;
  }
  .back-brand .brand__square { width: 18px; height: 18px; }
  .back-brand .brand__name { font-size: 12px; }
</style>
</head>
<body>

<section class="card card--front" aria-label="Business card front">
  <div class="corner-tab"></div>

  <div class="person">
    <p class="person__name">Glen R. Harlow</p>
    <p class="person__title">Small Business Advisor</p>
  </div>

  <div class="brand">
    <span class="brand__square"></span>
    <span class="brand__name">Bayfield Capital Works</span>
  </div>
  <p class="brand__tagline">Trusted guidance for every local business sale</p>

  <p class="address">P.O. Box 418 Harbor Road<br>Bayfield ON, K0A 2B4</p>

  <ul class="contacts">
    <li>
      <svg viewBox="0 0 12 12" aria-hidden="true"><path fill="#8cc63f" d="M2.5 1h2l1 3-1.3 1a7 7 0 0 0 2.8 2.8L8 6.5l3 1v2A1.5 1.5 0 0 1 9.5 11 8.5 8.5 0 0 1 1 2.5 1.5 1.5 0 0 1 2.5 1z"/></svg>
      (555) 274-3918
    </li>
    <li>
      <svg viewBox="0 0 12 12" aria-hidden="true"><rect x="3" y="0.5" width="6" height="11" rx="1" fill="none" stroke="#8cc63f" stroke-width="1.3"/><circle cx="6" cy="9.5" r="0.7" fill="#8cc63f"/></svg>
      (555) 806-2147
    </li>
    <li>
      <svg viewBox="0 0 12 12" aria-hidden="true"><rect x="0.5" y="2" width="11" height="8" fill="#8cc63f"/><path d="M0.5 2l5.5 4.5L11.5 2" fill="none" stroke="#1b3a6d" stroke-width="1"/></svg>
      g.harlow@bayfieldcapitalworks.example
    </li>
    <li>
      <svg viewBox="0 0 12 12" aria-hidden="true"><circle cx="6" cy="6" r="5.3" fill="none" stroke="#8cc63f" stroke-width="1.2"/><ellipse cx="6" cy="6" rx="2.3" ry="5.3" fill="none" stroke="#8cc63f" stroke-width="1"/><path d="M0.7 6h10.6" stroke="#8cc63f" stroke-width="1"/></svg>
      www.bayfieldcapitalworks.example
    </li>
  </ul>

  <div class="edge-band edge-band--green"></div>
  <div class="edge-band edge-band--white"></div>
</section>

<section class="card card--back" aria-label="Business card back">
  <div class="back-pattern" role="img" aria-label="Embossed repeating chevron pattern in tones of navy and light blue"></div>
  <div class="back-brand">
    <span class="brand__square"></span>
    <span class="brand__name">Bayfield Capital Works</span>
  </div>
</section>

</body>
</html>
```